Marketing - Outdoor Vinyl banner, Outdoor Poster, Flyer modifications

Hi, I worked with you in the past and attached flyer designs. It just needs to be tweaked for various prints.
1)Outdoor vinyl banner (4 feet height and 8 feet width) print: Just grand opening pic, logo with name, tagline and call/text us portion.
2)Outdoor Poster (5 feet height and 3 feet width) print: same as above
3) Indoor poster for both horizontal & Vertical prints: Just logo w/ name, tagline, "We are MOVING Next door"
4)Flyer: will give minor modifications to attached flyer designs

```html
<!DOCTYPE html>
<html lang="en">
<head>
<meta charset="utf-8">
<title>Bright Arc Dentistry – Moving Banner</title>
<link rel="stylesheet" href="https://fonts.googleapis.com/css2?family=Playfair+Display:wght@400;700;900&display=swap">
<style>
  :root {
    --cyan: #0cb1d9;
    --slate: #627b97;
    --white: #ffffff;
    --page: #ffffff;
    --serif: "Playfair Display", Georgia, serif;
  }
  html, body {
    margin: 0;
    padding: 0;
    width: 1200px;
    height: 1200px;
    overflow: hidden;
    background: var(--page);
  }
  .canvas {
    position: relative;
    width: 1200px;
    height: 1200px;
  }
  .banner {
    position: absolute;
    left: 110px;
    top: 281px;
    width: 1025px;
    height: 626px;
    overflow: hidden;
    background: var(--white);
    font-family: var(--serif);
  }
  .banner-waves {
    position: absolute;
    inset: 0;
    width: 100%;
    height: 100%;
    display: block;
  }
  .brand {
    position: absolute;
    top: 34px;
    left: 0;
    right: 0;
    display: flex;
    justify-content: center;
    align-items: center;
    gap: 18px;
    color: var(--cyan);
    font-weight: 700;
  }
  .brand-mark {
    width: 76px;
    height: 76px;
    border-radius: 50%;
    background: var(--cyan);
    flex: none;
  }
  .brand-name {
    display: flex;
    flex-direction: column;
    line-height: 1;
  }
  .brand-name .line-top {
    font-size: 28px;
    letter-spacing: 14px;
    margin-bottom: 6px;
  }
  .brand-name .line-main {
    font-size: 60px;
    letter-spacing: 2px;
  }
  .headline {
    position: absolute;
    left: 0;
    right: 0;
    text-align: center;
    color: var(--white);
    margin: 0;
    line-height: 1;
  }
  .headline-intro {
    top: 287px;
    font-size: 79px;
    font-weight: 400;
  }
  .headline-main {
    top: 362px;
    font-size: 156px;
    font-weight: 900;
    letter-spacing: -2px;
  }
  .tagline {
    position: absolute;
    left: 0;
    right: 0;
    top: 540px;
    margin: 0;
    text-align: center;
    color: var(--white);
    font-size: 64px;
    font-weight: 700;
    line-height: 1;
  }
</style>
</head>
<body>
<div class="canvas">
  <section class="banner">
    <svg class="banner-waves" viewBox="177 452 1651 1008" preserveAspectRatio="none" aria-hidden="true">
      <path fill="var(--slate)" d="M177,718 C330,840 500,880 680,873 L1130,783 C1400,712 1650,662 1828,722 L1828,1460 L177,1460 Z"/>
      <path fill="var(--cyan)" stroke="var(--white)" stroke-width="4" d="M177,792 C330,890 520,895 700,872 C1000,830 1300,742 1520,736 C1650,733 1750,755 1828,788 L1828,1358 Q1000,1170 177,1364 Z"/>
      <path fill="var(--white)" d="M177,1364 Q1000,1170 1828,1358 L1828,1460 L177,1460 Z"/>
      <path fill="var(--slate)" d="M177,1364 Q1000,1236 1828,1358 L1828,1460 L177,1460 Z"/>
    </svg>

    <header class="brand">
      <span class="brand-mark"></span>
      <span class="brand-name">
        <span class="line-top">BRIGHT ARC</span>
        <span class="line-main">DENTISTRY</span>
      </span>
    </header>

    <h1 class="headline headline-intro">We’re MOVING</h1>
    <p class="headline headline-main">Next DOOR!</p>
    <p class="tagline">Exciteed to find home!</p>
  </section>
</div>
</body>
</html>
```